Zimbal, a future commerce website

Zimbal will be a commerce website; the project is quite large, and for now I just require three pages and the main bar to be crafted; If chosen your design, I will require you to work with me in a freelance job for the rest of the site to be made.
The following is one way to put Zimbal’s building blocks; you can propose another.
A list of webpages, whose design I like, is in the first document.
-Design specification
Zimbal’s interface should be minimal and intuitive.
Its design should make the user perceive Zimbal as innovative; I will incline for an out of the box design.
--Main bar
It will contain the site logo, a search bar, and four buttons, listed below.
---Notifications button
It will display a sidebar with containers; each container will have an icon, the notification, and one or two buttons; two example notifications and its respective buttons are in the second document.
It shall stand out when there are unseen notifications.
---Shopping cart button
A sidebar will be toggled on click with added product previews.
---Sell Button
---Account button
When clicked it will display a pane whose elements will depend on the user
status.
----If logged
It will display seller’s store image, a button linking to the main section of the account section, a button linking to in-process bought items of the account section, and a button linking to in-process sold items of the account section.
----If not logged
It will contain the elements for the user to either log in or register; for the former, email or username and password will be asked, for the latter, username, email, and password, this last one being asked twice.
--Product previews
Each, will have a title, a product image, and the product’s most important characteristics; most characteristics will have alongside an icon, which will display on mouse over the characteristic name, or, a name. Characteristics of two product categories whose product previews will contain an icon alongside are in the third document.
--Main page
Product previews of several categories will be displayed here; in order to reflect recommendation, some should have distinct size.
A list of categories will be present in this page; it may be toggled by a button contained in the main bar, or be displayed permanently.
A text conveying the message that all purchases made with Zimbal payment system are protected will be contained in a full width element which will be positioned below the main bar of this page; a “Learn more” link will be positioned in this element.
--Product page creation page
It will be displayed as part of the publication page.
It will be a "what you see is what you get" design system; the user will choose from several templates and fill the appropriate spaces; where text must be put, sample text will be present, and, where an image must, a plus sign and a “Add image” text will be present; submit please two templates; for the user to be able to add more content, at the bottom of the template there will be four layouts, upon click of one, it will be added.
Regarding the shipping menu, there will always be an empty box with a plus sign and a “Add shipping option” text, if clicked the user will be able to either fill it with company name, shipping time, and price, or to put the text “Arrange with seller” in it (if there is no other box with that text).
--Product page
It will not occupy the whole viewport; there will be vertical holes at the leftmost and rightmost parts of the viewport.
It will contain: price (which should include shipping in type one publications), sale price (for some product pages), countdown of sale price, average seller’s handling time, seller’s reputation indicator as measured by percentage of positive reviews received, seller’s store/profile image, seller’s username, a shipping menu consisting of boxes (selected will be displayed differently), “Buy” and “Add to cart” buttons, a section to view and ask questions, and seller provided images and text.
Previews of similar products will also be present.
Reason: Designs still require some work

```html
<!DOCTYPE html>
<html lang="en">
<head>
<meta charset="utf-8">
<title>Zimbal — Store</title>
<link href="https://fonts.googleapis.com/css2?family=Open+Sans:wght@400;600;700;800&display=swap" rel="stylesheet">
<style>
:root{
  --orange:#f47c20;
  --orange-soft:#fdebdc;
  --ink:#2b2b2b;
  --dark:#333333;
  --darker:#222222;
  --text:#555555;
  --muted:#999999;
  --line:#e3e3e3;
  --bg:#ffffff;
  --blue:#29a8e0;
}
*{box-sizing:border-box;margin:0;padding:0}
html,body{width:865px;height:1200px;overflow:hidden}
body{font-family:"Open Sans",Arial,sans-serif;color:var(--text);background:var(--bg);font-size:10px;position:relative}
a{color:inherit;text-decoration:none}
ul{list-style:none}

.top-strip{height:22px;background:var(--darker);color:#ccc;font-size:9px;display:flex;justify-content:flex-end;align-items:center;gap:16px;padding-right:72px}

.masthead{height:70px;display:flex;align-items:center;gap:14px;padding:0 72px}
.brand{display:flex;align-items:center;gap:8px;margin-right:auto}
.brand-mark{width:14px;height:14px;background:var(--orange)}
.brand-name{font-size:28px;font-weight:800;color:var(--orange);letter-spacing:-.5px}
.search{display:flex;height:30px;background:var(--darker);width:290px;align-items:center;padding:0 4px;gap:5px}
.search-label{color:#fff;font-weight:700;font-size:10px;padding:0 6px}
.search-cat{background:#fff;height:20px;width:66px;font-size:8px;color:var(--ink);display:flex;align-items:center;padding-left:5px}
.search-input{flex:1;height:20px;background:#fff}
.search-btn{width:22px;height:20px;background:var(--orange)}
.bar-actions{display:flex;align-items:center;gap:6px}
.bar-btn{position:relative;width:30px;height:30px;border:1px solid var(--line);display:flex;align-items:center;justify-content:center}
.bar-btn .dot{position:absolute;top:4px;right:5px;width:7px;height:7px;border-radius:50%;background:var(--orange);border:1px solid #fff}
.bar-sell{height:30px;padding:0 12px;background:var(--orange);color:#fff;font-weight:700;font-size:10px;display:flex;align-items:center}

.main-nav{height:26px;background:var(--orange);display:flex;align-items:center;padding:0 72px;color:#fff;font-weight:700;font-size:9px}
.main-nav ul{display:flex;gap:26px}
.cart-info{margin-left:auto;display:flex;gap:10px;align-items:center}

.protection{height:24px;background:var(--orange-soft);display:flex;align-items:center;justify-content:center;gap:8px;font-size:9px;color:var(--ink)}
.protection a{color:var(--orange);font-weight:700;text-decoration:underline}

.hero{height:258px;position:relative;background:linear-gradient(90deg,#5a6b78 0%,#8fa0aa 30%,#d9d4c6 55%,#eee9dd 100%)}
.hero-photo{position:absolute;left:0;top:0;width:55%;height:100%;background:linear-gradient(110deg,#3d4c59,#7a8c98 60%,rgba(200,195,180,0))}
.hero-copy{position:absolute;left:470px;top:70px}
.hero-copy h1{font-weight:400;font-size:30px;color:var(--ink);line-height:1.1}
.hero-copy h1 strong{display:block;color:var(--orange);font-weight:800;font-size:40px;letter-spacing:1px}
.btn-sell{display:inline-block;margin-top:16px;background:var(--darker);color:#fff;font-weight:700;font-size:11px;padding:8px 18px}
.hero-arrow{position:absolute;top:114px;width:22px;height:30px;background:rgba(0,0,0,.35)}
.hero-arrow.prev{left:0}.hero-arrow.next{right:0}

.content{display:flex;gap:25px;padding:22px 72px 0;height:590px}
.sidebar{width:175px}
.cat-box{border:1px solid var(--line)}
.cat-box h3{background:var(--orange);color:#fff;font-size:9px;font-weight:700;padding:8px 10px}
.cat-box li{font-size:8.5px;color:var(--ink);padding:8px 10px;border-top:1px solid var(--line)}
.promo{margin-top:14px;border:1px solid var(--line);padding:10px}
.promo h4{font-size:13px;font-weight:800;color:var(--ink)}
.promo p{font-size:8.5px;color:var(--orange);font-weight:600;margin:3px 0 8px}
.promo-img{height:80px;background:linear-gradient(135deg,#e45a8a,#4aa3d8 50%,#f2c94c)}

.shop{flex:1}
.perks{display:flex;gap:20px;height:46px}
.perk{flex:1;display:flex;align-items:center;gap:12px;justify-content:center}
.perk b{display:block;font-size:14px;font-weight:800}
.perk span{font-size:9px;color:var(--muted)}
.perk.ship b{color:var(--orange)}
.perk.happy b{color:var(--blue)}

.grid{display:grid;grid-template-columns:repeat(3,1fr);gap:14px 18px;margin-top:14px}
.card{border:1px solid var(--line);text-align:center;height:248px;position:relative;padding:8px}
.card-img{height:108px;border-radius:2px}
.tone-a{background:linear-gradient(135deg,#f5f5f5,#cfcfcf)}
.tone-b{background:radial-gradient(circle,#c7262e 0,#6a1317 35%,#f3f3f3 60%)}
.tone-c{background:linear-gradient(160deg,#2f6fb0,#9fd0ef 60%,#f1f1f1)}
.tone-d{background:radial-gradient(circle,#c0652a 0,#7a3e18 35%,#f3f3f3 65%)}
.tone-e{background:radial-gradient(circle,#2b2b2b 0,#555 30%,#f3f3f3 62%)}
.tone-f{background:radial-gradient(circle,#a8231d 0,#3a1a18 35%,#f3f3f3 62%)}
.card h5{font-size:10px;font-weight:700;color:var(--ink);margin-top:9px}
.card p{font-size:8px;color:var(--muted);margin:4px 8px;line-height:1.35}
.specs{display:flex;justify-content:center;gap:8px;margin-top:5px}
.spec{display:flex;align-items:center;gap:3px;font-size:7.5px;color:var(--ink)}
.spec svg{flex:none}
.price{font-size:9px;margin-top:6px}
.price s{color:var(--muted);margin-right:8px}
.price b{color:var(--orange)}
.quick{position:absolute;left:8px;right:8px;top:94px;background:rgba(0,0,0,.7);color:#fff;font-size:8px;padding:5px 0}
.card-actions{display:flex;gap:4px;justify-content:center;margin-top:6px}
.card-actions a{font-size:7.5px;padding:4px 8px;color:#fff;background:var(--darker)}
.card-actions a.add{background:var(--orange)}
.badge{position:absolute;top:4px;right:4px;background:var(--orange);color:#fff;font-size:7px;padding:2px 5px}

.newsletter{position:absolute;top:990px;left:0;width:865px;height:55px;background:var(--dark);display:flex;align-items:center;padding:0 72px;gap:14px;color:#fff}
.socials{display:flex;gap:10px}
.socials i{width:12px;height:12px;border-radius:50%;background:#888;display:block}
.nl-title b{display:block;font-size:11px;font-weight:800}
.nl-title span{font-size:7.5px;color:#bbb}
.nl-form{margin-left:auto;display:flex}
.nl-input{width:170px;height:22px;background:#fff}
.nl-btn{background:var(--orange);font-size:8px;font-weight:700;padding:0 12px;display:flex;align-items:center}

.footer{position:absolute;top:1045px;left:0;width:865px;height:133px;display:flex;gap:30px;padding:18px 72px 0}
.footer-col h6{font-size:10px;font-weight:800;color:var(--ink);margin-bottom:8px}
.footer-col li{font-size:8px;margin-bottom:5px}
.footer-about{width:170px}
.footer-about .brand-name{font-size:22px}
.footer-about p{font-size:8px;line-height:1.4;margin-top:4px}
.footer-col.contact{margin-left:auto;width:170px}
.cards{display:flex;gap:4px;margin-top:4px}
.cards i{width:22px;height:13px;background:#cfd6dd;display:block}
.copyright{position:absolute;top:1178px;left:0;width:865px;height:22px;background:var(--darker);color:#aaa;font-size:8px;display:flex;align-items:center;justify-content:center}
</style>
</head>
<body>
<div class="top-strip"><span>My Account</span><span>Checkout</span><span>English</span><span>USD</span></div>

<header class="masthead">
  <a class="brand" href="#"><span class="brand-mark"></span><span class="brand-name">Zimbal</span></a>
  <div class="search"><span class="search-label">Search</span><span class="search-cat">All Category ▾</span><span class="search-input"></span><span class="search-btn"></span></div>
  <div class="bar-actions">
    <a class="bar-btn" href="#" aria-label="Notifications">
      <svg width="14" height="15" viewBox="0 0 14 15"><path d="M7 1a4 4 0 0 1 4 4v4l2 2H1l2-2V5a4 4 0 0 1 4-4z" fill="#333"/><circle cx="7" cy="13" r="1.6" fill="#333"/></svg>
      <span class="dot"></span>
    </a>
    <a class="bar-btn" href="#" aria-label="Shopping cart">
      <svg width="16" height="14" viewBox="0 0 16 14"><path d="M1 1h2.5l2 8h8l1.5-6H4.5" fill="none" stroke="#333" stroke-width="1.6"/><circle cx="6.5" cy="12" r="1.3" fill="#333"/><circle cx="12.5" cy="12" r="1.3" fill="#333"/></svg>
    </a>
    <a class="bar-sell" href="#">Sell</a>
    <a class="bar-btn" href="#" aria-label="Account">
      <svg width="14" height="14" viewBox="0 0 14 14"><circle cx="7" cy="4" r="3" fill="#333"/><path d="M1 14a6 6 0 0 1 12 0z" fill="#333"/></svg>
    </a>
  </div>
</header>

<nav class="main-nav">
  <ul><li>HOME</li><li>SHOP</li><li>BLOG</li><li>SHORTCODES</li><li>FEATURES</li><li>PAGES</li><li>ABOUT US</li><li>CONTACT US</li></ul>
  <div class="cart-info"><span>$0.00</span><span>0 items</span></div>
</nav>

<div class="protection">
  <svg width="11" height="12" viewBox="0 0 11 12"><path d="M5.5 0 11 2v4c0 3-2.5 5-5.5 6C2.5 11 0 9 0 6V2z" fill="#f47c20"/><path d="M3 6l2 2 3-4" fill="none" stroke="#fff" stroke-width="1.3"/></svg>
  <span>Every purchase made with Zimbal payments is fully protected.</span>
  <a href="#">Learn more</a>
</div>

<section class="hero">
  <div class="hero-photo" role="img" aria-label="Young man in a denim shirt looking at his phone outdoors"></div>
  <span class="hero-arrow prev"></span><span class="hero-arrow next"></span>
  <div class="hero-copy">
    <h1>Zimbal as <strong>INNOVATIVE</strong></h1>
    <a class="btn-sell" href="#">Sell Now</a>
  </div>
</section>

<main class="content">
  <aside class="sidebar">
    <div class="cat-box">
      <h3>PRODUCT CATEGORIES</h3>
      <ul><li>ORBIT PHONE</li><li>KESTREL PHONE</li><li>BEST MOBILES</li><li>CAR PHONE</li><li>ELECTRONICS</li><li>LAPTOP</li><li>SHOES</li><li>MORE</li></ul>
    </div>
    <div class="promo">
      <h4>GET A NEW VIREO !</h4>
      <p>Up to 50% off on all items</p>
      <div class="promo-img" role="img" aria-label="Row of colourful smartphones"></div>
    </div>
  </aside>

  <section class="shop">
    <div class="perks">
      <div class="perk ship">
        <svg width="34" height="24" viewBox="0 0 34 24"><rect x="1" y="3" width="20" height="14" fill="#f47c20"/><path d="M21 7h7l5 5v5H21z" fill="#f47c20"/><circle cx="8" cy="19" r="3.5" fill="#fff" stroke="#f47c20" stroke-width="2"/><circle cx="27" cy="19" r="3.5" fill="#fff" stroke="#f47c20" stroke-width="2"/></svg>
        <div><b>FREE SHIPPING</b><span>ON ALL ITEMS</span></div>
      </div>
      <div class="perk happy">
        <svg width="28" height="24" viewBox="0 0 28 24"><path d="M14 23 3 12A6.5 6.5 0 0 1 14 4a6.5 6.5 0 0 1 11 8z" fill="#29a8e0"/></svg>
        <div><b>100% SATISFACTION</b><span>GUARANTEED</span></div>
      </div>
    </div>

    <div class="grid">
      <article class="card">
        <div class="card-img tone-a" role="img" aria-label="Tablet in a dark case"></div>
        <span class="quick">Quick View</span>
        <h5>Josen maset gasten</h5>
        <p>A long and detailed screencast by Tomas Ferlin</p>
        <div class="specs"><span class="spec"><svg width="8" height="10" viewBox="0 0 8 10"><rect x=".5" y=".5" width="7" height="9" rx="1" fill="none" stroke="#f47c20"/></svg>10"</span><span class="spec"><svg width="10" height="8" viewBox="0 0 10 8"><rect x=".5" y="1" width="8" height="6" fill="none" stroke="#f47c20"/><rect x="9" y="3" width="1" height="2" fill="#f47c20"/></svg>12h</span></div>
        <div class="card-actions"><a href="#">Buy Now</a><a class="add" href="#">Add to cart</a></div>
      </article>
      <article class="card">
        <div class="card-img tone-b" role="img" aria-label="Red compact camera"></div>
        <h5>Josen maset gasten</h5>
        <p>A long and detailed screencast by Tomas Ferlin</p>
        <div class="specs"><span class="spec"><svg width="10" height="8" viewBox="0 0 10 8"><rect x=".5" y="1.5" width="9" height="6" fill="none" stroke="#f47c20"/><circle cx="5" cy="4.5" r="1.6" fill="#f47c20"/></svg>20MP</span><span class="spec"><svg width="9" height="9" viewBox="0 0 9 9"><circle cx="4.5" cy="4.5" r="4" fill="none" stroke="#f47c20"/><path d="M4.5 2v3h2" fill="none" stroke="#f47c20"/></svg>5x</span></div>
        <div class="price"><s>$30.00</s><b>$23.00</b></div>
      </article>
      <article class="card">
        <span class="badge">Sale</span>
        <div class="card-img tone-c" role="img" aria-label="Desktop monitor"></div>
        <h5>Josen maset gasten</h5>
        <p>A long and detailed screencast by Tomas Ferlin</p>
        <div class="specs"><span class="spec"><svg width="10" height="9" viewBox="0 0 10 9"><rect x=".5" y=".5" width="9" height="6" fill="none" stroke="#f47c20"/><path d="M3 8.5h4" stroke="#f47c20"/></svg>24"</span><span class="spec"><svg width="9" height="9" viewBox="0 0 9 9"><path d="M1 8 4.5 1 8 8z" fill="none" stroke="#f47c20"/></svg>4K</span></div>
        <div class="price"><s>$30.00</s><b>$23.00</b></div>
      </article>
      <article class="card">
        <div class="card-img tone-d" role="img" aria-label="Brown leather shoulder bag"></div>
        <h5>Josen maset gasten</h5>
        <p>A long and detailed screencast by Tomas Ferlin</p>
        <div class="specs"><span class="spec"><svg width="9" height="9" viewBox="0 0 9 9"><rect x=".5" y="3" width="8" height="5.5" fill="none" stroke="#f47c20"/><path d="M3 3V1h3v2" fill="none" stroke="#f47c20"/></svg>Leather</span><span class="spec"><svg width="9" height="9" viewBox="0 0 9 9"><circle cx="4.5" cy="4.5" r="4" fill="#f47c20"/></svg>Brown</span></div>
        <div class="price"><s>$30.00</s><b>$23.00</b></div>
      </article>
      <article class="card">
        <div class="card-img tone-e" role="img" aria-label="Black camera with red accent"></div>
        <h5>Josen maset gasten</h5>
        <p>A long and detailed screencast by Tomas Ferlin</p>
        <div class="specs"><span class="spec"><svg width="10" height="8" viewBox="0 0 10 8"><rect x=".5" y="1.5" width="9" height="6" fill="none" stroke="#f47c20"/><circle cx="5" cy="4.5" r="1.6" fill="#f47c20"/></svg>24MP</span><span class="spec"><svg width="9" height="9" viewBox="0 0 9 9"><circle cx="4.5" cy="4.5" r="4" fill="none" stroke="#f47c20"/><path d="M4.5 2v3h2" fill="none" stroke="#f47c20"/></svg>10x</span></div>
        <div class="price"><s>$30.00</s><b>$23.00</b></div>
      </article>
      <article class="card">
        <div class="card-img tone-f" role="img" aria-label="Red over-ear headphones"></div>
        <h5>Josen maset gasten</h5>
        <p>A long and detailed screencast by Tomas Ferlin</p>
        <div class="specs"><span class="spec"><svg width="10" height="8" viewBox="0 0 10 8"><rect x=".5" y="1" width="8" height="6" fill="none" stroke="#f47c20"/><rect x="9" y="3" width="1" height="2" fill="#f47c20"/></svg>30h</span><span class="spec"><svg width="9" height="9" viewBox="0 0 9 9"><path d="M1 3h2l3-2v7L3 6H1z" fill="#f47c20"/></svg>Bass</span></div>
        <div class="price"><s>$30.00</s><b>$23.00</b></div>
      </article>
    </div>
  </section>
</main>

<section class="newsletter">
  <div class="socials"><i></i><i></i><i></i><i></i><i></i></div>
  <svg width="22" height="16" viewBox="0 0 22 16"><rect x="1" y="1" width="20" height="14" fill="none" stroke="#fff" stroke-width="1.5"/><path d="M1 1l10 8 10-8" fill="none" stroke="#fff" stroke-width="1.5"/></svg>
  <div class="nl-title"><b>SIGN UP FOR OUR NEWSLETTER</b><span>Get the latest deals and new arrivals first</span></div>
  <div class="nl-form"><span class="nl-input"></span><span class="nl-btn">SUBSCRIBE</span></div>
</section>

<footer class="footer">
  <div class="footer-col footer-about">
    <span class="brand-name">Zimbal</span>
    <p>Zimbal brings smart shopping to everyone with fair prices, safe payments and fast delivery on every order.</p>
  </div>
  <div class="footer-col">
    <h6>MY ACCOUNT</h6>
    <ul><li>› About us</li><li>› My Account</li><li>› Checkout</li><li>› Wish List</li><li>› Product Listing</li></ul>
  </div>
  <div class="footer-col">
    <h6>INFORMATION</h6>
    <ul><li>› About Us</li><li>› Terms of Use</li><li>› Help &amp; Support</li><li>› Privacy Policy</li><li>› Contact Us</li></ul>
  </div>
  <div class="footer-col contact">
    <h6>CONTACT US</h6>
    <ul><li>12 Harbour Lane, Westfield 40215</li><li>Telephone: (555) 014-2280</li><li>E-mail: hello@zimbal-shop.example</li></ul>
    <div class="cards"><i></i><i></i><i></i><i></i><i></i></div>
  </div>
</footer>
<div class="copyright">Copyright © 2024 Zimbal. All Rights Reserved.</div>
</body>
</html>
```